Website & Logo The full package New Business new design and idea

Word Press

Simple, clean and very professional and approachable if possible

I am looking for a full business concept from logo to colour pallet and everything in between.
Brand new business concept, the successful applicant may continue on as our outsourced point person for all future work.

I will have an animated explainer video going over the four keys to business success Staff, Product & Services, Marketing, Sales and why the need a coach just like a sporting team to stay focused and clear on measurable outcomes.

Just added script (pdf attachment) i will be using for the explainer video at top of site.
Updates

Target Market(s)

Small business owners in Australia

Industry/Entity Type

Business Consultant

Number of Pages Required

1 page

Font styles to use
Sans Serif

Colors

Designer to choose colors to be used in the design.

Requirements
Must have
• Word press using Divi platform
• Ball park as per pdf uploaded
• Must work on all devices
• Social links
• Clear and straight forward movement through site
• Great capture of name and email,
• Free Download
• 10 Things you can start today in your small business to get you going again!
Nice to have
• clean one page potentially
• Free files and resources page
Should not have
• boring old menu and old framing

```html
<!DOCTYPE html>
<html lang="en">
<head>
<meta charset="utf-8">
<title>Bright Path Business Coach</title>
<link href="https://fonts.googleapis.com/css2?family=Lato:wght@400;700;900&display=swap" rel="stylesheet">
<style>
:root{
  --orange:#ee7a1c;
  --orange-dark:#d9650f;
  --navy:#0f2a4f;
  --charcoal:#2b2b2b;
  --blue:#1fa3d6;
  --green:#3f7a2a;
  --footer:#262626;
  --ink:#222;
  --muted:#555;
  --panel:#eeeeee;
  --white:#fff;
}
*{box-sizing:border-box;margin:0;padding:0}
html,body{width:1200px;height:4358px;overflow:hidden}
body{font-family:"Lato",sans-serif;color:var(--ink);background:var(--white);position:relative}
section,header,footer,nav{position:relative;width:1200px}
.btn{display:inline-block;border-radius:30px;font-weight:700;font-size:13px;letter-spacing:.5px;text-transform:uppercase;text-align:center}
.btn-blue{background:var(--blue);color:#fff;width:156px;height:32px;line-height:32px}
.btn-outline{border:2px solid #fff;color:#fff}
/* header */
.topbar{height:87px}
.brand{position:absolute;left:150px;top:18px;display:flex;align-items:center;gap:12px}
.brand-dot{width:44px;height:44px;border-radius:50%;background:var(--orange)}
.brand-name{color:var(--orange);font-weight:900;font-size:20px;line-height:23px;text-transform:uppercase;white-space:nowrap}
.contact{position:absolute;top:22px;display:flex;gap:12px;align-items:center;font-size:13px;color:var(--ink)}
.contact .ico{width:38px;height:38px;background:var(--navy);border-radius:4px;display:flex;align-items:center;justify-content:center}
.contact small{display:block;color:var(--orange);font-size:12px}
.nav{height:44px;background:var(--orange);display:flex;justify-content:center;gap:42px;align-items:center;color:#fff;font-size:14px;font-weight:700}
/* hero */
.hero{height:561px;background:linear-gradient(160deg,#3a3a3a,#1a1a1a 55%,#2e2a26);color:#fff;text-align:center}
.hero-side{position:absolute;left:60px;top:140px;display:flex;flex-direction:column;align-items:center;gap:22px}
.hero-side span{width:12px;height:12px;border-radius:50%;background:#fff}
.hero-side .follow{writing-mode:vertical-rl;transform:rotate(180deg);font-size:13px;margin-top:30px;font-style:normal}
.play{position:absolute;left:576px;top:160px;width:48px;height:48px;border:2px solid #fff;border-radius:50%;display:flex;align-items:center;justify-content:center}
.hero h1{position:absolute;left:0;width:1200px;top:212px;font-size:50px;font-weight:900;letter-spacing:1px}
.hero p{position:absolute;left:300px;width:600px;top:280px;font-size:19px;font-weight:700;line-height:26px}
.hero .btn{position:absolute;left:502px;top:350px;width:196px;height:46px;line-height:42px;font-size:16px;text-transform:none}
.dots{position:absolute;right:66px;top:240px;display:flex;flex-direction:column;gap:22px;align-items:center}
.dots span{width:10px;height:10px;border-radius:50%;background:#fff}
.dots .on{width:20px;height:20px;border:3px solid #fff;background:transparent}
/* welcome */
.welcome{height:398px}
.welcome h2{position:absolute;left:145px;top:72px;font-size:34px;font-weight:900}
.welcome .lead{position:absolute;left:145px;top:124px;width:580px;font-size:15px;line-height:24px}
.welcome .small{position:absolute;left:145px;top:240px;width:600px;font-size:12px;line-height:19px;color:var(--muted)}
.welcome-photo{position:absolute;left:814px;top:78px;width:238px;height:238px;border-radius:50%;background:radial-gradient(circle at 40% 40%,#f1e6ee,#cfa9bb 60%,#a1687e)}
/* snapshot */
.snapshot{height:494px;background:var(--orange);color:#fff;text-align:center}
.snapshot h2{position:absolute;top:76px;width:1200px;font-size:34px;font-weight:700}
.snapshot .intro{position:absolute;left:160px;width:880px;top:125px;font-size:16px;line-height:24px}
.snapshot h3{position:absolute;top:244px;width:1200px;font-size:26px;font-weight:700}
.stats{position:absolute;left:145px;top:296px;display:flex;gap:20px}
.stat{width:216px;height:163px;background:var(--charcoal);padding-top:22px}
.stat b{display:block;font-size:52px;font-weight:900}
.stat span{display:block;font-size:12px;line-height:18px;margin:14px 30px 0}
/* offers */
.offers{height:459px}
.cards{position:absolute;left:145px;top:43px;display:flex;gap:20px}
.card{width:291px;height:335px;padding:28px 24px;color:#fff}
.card h4{font-size:21px;font-weight:700;line-height:27px;height:100px}
.card p{font-size:12px;line-height:19px;height:130px}
.card .btn{border-radius:0;border:1px solid #fff;width:90px;height:32px;line-height:30px;font-size:11px;text-transform:none;font-weight:400}
.navy{background:var(--navy)}.orng{background:var(--orange-dark)}.dark{background:var(--charcoal)}
/* how */
.how{height:398px}
.how-panel{position:absolute;left:0;top:0;width:1055px;height:334px;background:var(--panel);border-radius:0 30px 30px 0}
.how h2{position:absolute;left:145px;top:86px;font-size:34px;font-weight:900}
.how p{position:absolute;left:145px;top:140px;width:470px;font-size:13px;line-height:20px}
.how .btn{position:absolute;left:145px;top:234px}
.how-art{position:absolute;left:697px;top:49px;width:263px;height:248px;background:linear-gradient(180deg,#f6f6f6,#d9d9d9);border-radius:6px}
/* activates */
.activates{height:336px;text-align:center}
.activates .intro{position:absolute;left:150px;width:900px;top:10px;font-size:13px;line-height:20px}
.activates h4{position:absolute;top:62px;width:1200px;color:var(--orange);font-size:17px;font-weight:700}
.list{position:absolute;top:95px;text-align:left;list-style:none;font-size:12px;line-height:20px;width:460px}
.list li{position:relative;padding-left:20px;margin-bottom:3px}
.list li::before{content:"";position:absolute;left:0;top:5px;width:10px;height:10px;border-radius:50%;background:var(--orange)}
.activates .btn{position:absolute;left:522px;top:258px}
/* application */
.application{height:422px;background:linear-gradient(100deg,#f08a2c,#e8731a 45%,#f39a3a);color:#fff;text-align:center}
.application h2{position:absolute;top:80px;width:1200px;font-size:36px;font-weight:700}
.application p{position:absolute;left:220px;width:760px;font-size:18px;line-height:27px}
.application .btn{position:absolute;left:506px;top:285px;width:188px;height:48px;line-height:44px;font-size:17px}
/* about */
.about{height:610px}
.about h2{position:absolute;left:145px;top:180px;font-size:34px;font-weight:900}
.about p{position:absolute;left:145px;top:236px;width:430px;font-size:13px;line-height:21px}
.about .btn{position:absolute;left:145px;top:372px}
.about-shape{position:absolute;left:610px;top:150px;width:440px;height:360px;background:var(--orange);clip-path:polygon(18% 0,100% 0,82% 100%,0 100%)}
.about-photo{position:absolute;left:690px;top:68px;width:290px;height:445px;background:linear-gradient(180deg,#c9b7a6,#2a3448 55%,#1c2434);border-radius:120px 120px 0 0}
/* newsletter */
.newsletter{height:290px;background:var(--green);color:#fff;text-align:center}
.newsletter h2{position:absolute;top:60px;width:1200px;font-size:32px;font-weight:700}
.newsletter p{position:absolute;left:230px;width:740px;top:110px;font-size:13px;line-height:20px}
.form{position:absolute;left:274px;top:175px;display:flex;gap:18px}
.field{width:210px;height:44px;border-radius:24px;background:#fff;color:#888;font-size:12px;text-align:left;padding:14px 24px}
.field.wide{width:265px}
.form .btn{background:var(--orange);color:#fff;width:145px;height:44px;line-height:44px;font-size:16px;text-transform:none}
/* footer */
.footer{height:261px;background:var(--footer);color:#fff;text-align:center;font-size:14px}
.f-contacts{position:absolute;top:44px;width:1200px;display:flex;justify-content:center;gap:64px}
.f-contacts span{display:flex;align-items:center;gap:8px}
.socials{position:absolute;top:92px;width:1200px;display:flex;justify-content:center;gap:10px}
.socials span{width:40px;height:40px;border-radius:50%;background:#fff}
.f-links{position:absolute;top:156px;width:1200px}
.copy{position:absolute;top:200px;width:1200px;font-size:13px}
</style>
</head>
<body>

<header class="topbar">
  <div class="brand"><span class="brand-dot"></span><span class="brand-name">Bright Path<br>Business Coach</span></div>
  <div class="contact" style="left:593px">
    <span class="ico"><svg width="18" height="18" viewBox="0 0 24 24"><path fill="#fff" d="M6.6 10.8a15 15 0 0 0 6.6 6.6l2.2-2.2c.3-.3.7-.4 1-.2 1.1.4 2.3.6 3.6.6.6 0 1 .4 1 1V20c0 .6-.4 1-1 1A17 17 0 0 1 3 4c0-.6.4-1 1-1h3.5c.6 0 1 .4 1 1 0 1.3.2 2.5.6 3.6.1.3 0 .7-.2 1z"/></svg></span>
    <div><small>Call us anytime</small>555 010 2040</div>
  </div>
  <div class="contact" style="left:775px">
    <span class="ico"><svg width="18" height="18" viewBox="0 0 24 24"><path fill="#fff" d="M3 5h18v14H3z"/><path fill="none" stroke="#0f2a4f" stroke-width="2" d="M3 6l9 7 9-7"/></svg></span>
    <div><small>Send us a mail</small>info@brightpathcoach.com</div>
  </div>
</header>

<nav class="nav"><span>Home</span><span>About Us</span><span>How It Works</span><span>Application</span><span>Pricing</span><span>Contact Us</span></nav>

<section class="hero" role="img" aria-label="Team meeting around an office table, dark photo backdrop">
  <div class="hero-side"><span></span><span></span><span></span><span></span><em class="follow">Follow us</em></div>
  <div class="play"><svg width="16" height="16" viewBox="0 0 20 20"><path fill="#fff" d="M6 3l11 7-11 7z"/></svg></div>
  <h1>BRIGHT PATH BUSINESS COACH</h1>
  <p>Sed ut perspiciatis unde omnis iste natus error sit voluptatem accusantium doloremque</p>
  <span class="btn btn-outline">&#8615; Free Download</span>
  <div class="dots"><span></span><span class="on"></span><span></span></div>
</section>

<section class="welcome">
  <h2>Welcome</h2>
  <p class="lead">Bright Path Business Coach is here to help, support and turn your small business around. It may not be easy, it may not be pretty, it may not be conventional or what you want to hear but my only goal is to help you succeed in your small business struggling in Australia.</p>
  <p class="small">I offer a 12 week fully supported and personally applied program, each week you complete the activities and we meet over a video call where your actions are accountable and measurable. Every business and small business owner are different, so not one solution fits all, and that's exactly why I can make it personal for those who want to change and need it to happen now...</p>
  <div class="welcome-photo" role="img" aria-label="Photo of a person planning on a wall board"></div>
</section>

<section class="snapshot">
  <h2>Australian Small Business Snapshot</h2>
  <p class="intro">It's an extremely sad sign of the times when you're confronted with a myriad of 'for lease' signs in shop windows along major shopping hubs. While most businesses in Australia are small — accounting for 97 percent of all businesses — they're shutting their doors in alarmingly high numbers.</p>
  <h3>What is the Small Business Failure Rate?</h3>
  <div class="stats">
    <div class="stat"><b>20%</b><span>of small businesses fail in their first year</span></div>
    <div class="stat"><b>30%</b><span>of small businesses fail in their second year</span></div>
    <div class="stat"><b>50%</b><span>of small businesses fail after five years in business</span></div>
    <div class="stat"><b>70%</b><span>Finally, 70% of small business owners fail in their 10th year in business</span></div>
  </div>
</section>

<section class="offers">
  <div class="cards">
    <div class="card navy"><h4>Giving Back Free</h4><p>Bright Path Business Coach is offering 4 FREE 12-week coaching one on one support programs every 3 months to struggling businesses in 2019 as our way of giving back and helping others in need. Just fill out the information sheet and we will let you know as soon as possible.</p><span class="btn">Learn More</span></div>
    <div class="card orng"><h4>Special Offer - Below Cost Price $200 a week for 12 weeks</h4><p>Bright Path Business Coach is offering this incredible one on one support program to only 12 small business owners in the first quarter in 2019 at below cost, so if you need help now, just fill out the information sheet and we will let you know as soon as possible.</p><span class="btn">Learn More</span></div>
    <div class="card dark"><h4>Just A Bit More $400 a week for 12 weeks</h4><p>Very limited on application only. Just 4 clients per quarter; here we provide additional one on one support each week and dive deeper into every element of your business and fast track the changes. Just fill out the information sheet and we will let you know as soon as possible.</p><span class="btn">Learn More</span></div>
  </div>
</section>

<section class="how">
  <div class="how-panel"></div>
  <h2>How it all works</h2>
  <p>With your permission I breakdown your business, Staff, Products / Services, Marketing and Sales. Under each of these four key components are up to 30 or more components including your staff training and experience, business financials...</p>
  <span class="btn btn-blue">Read More</span>
  <div class="how-art" role="img" aria-label="Illustration of a team meeting in front of a presentation chart"></div>
</section>

<section class="activates">
  <p class="intro">Regardless if you're a Bright Path Coach Free, Special Offer or Just a Bit More, Small Business Owner you all get one on one direct access to me each week along with mountains of accountable activities to turn your small business around into the dream you had hoped it could be.</p>
  <h4>Activates Include</h4>
  <ul class="list" style="left:145px">
    <li>Getting a measurable base line of the financials and existing marketing.</li>
    <li>Discussing the past ups and downs and looking forward to the future</li>
    <li>Understanding your product or service and how it fits into the current marketplace.</li>
    <li>Looking into the staff for potential opportunities or training.</li>
  </ul>
  <ul class="list" style="left:627px;width:430px">
    <li>Looking to establish a mastermind local group with a successful business</li>
    <li>Partnership opportunities</li>
    <li>Creating and applying marketing objectives</li>
    <li>How to give more to grow</li>
  </ul>
  <span class="btn btn-blue">Read More</span>
</section>

<section class="application" role="img" aria-label="Person working on a laptop, warm orange tinted photo">
  <h2>Application</h2>
  <p style="top:135px">Placements are strictly limited to 20 per quarter as they are all managed personally for the best possible outcomes.</p>
  <p style="top:198px">You must have internet access, put the time aside between 1-2 hours a week on a video call and be open to change and motivated and accountable to succeed with every scheduled meeting.</p>
  <span class="btn btn-outline">Get Started</span>
</section>

<section class="about">
  <h2>About Me</h2>
  <p>I am not superman, I just found myself absorbing information over the past 10 years through some mentors and personal development and saw so many small business owners struggling and I got sick of telling myself how I would change things that I eventually approached some businesses for free and asked if they needed a hand and they were over the moon...</p>
  <span class="btn btn-blue">Read More</span>
  <div class="about-shape"></div>
  <div class="about-photo" role="img" aria-label="Portrait photo of the business coach in a dark suit"></div>
</section>

<section class="newsletter">
  <h2>OUR NEWSLETTER</h2>
  <p>Sed ut perspiciatis unde omnis iste natus error sit voluptatem accusantium doloremque laudantium, totam rem aperiam, eaque ipsa quae ab illo inventore veritatis et quasi architecto beatae vitae dicta sunt explicabo.</p>
  <div class="form"><span class="field">Enter Name</span><span class="field wide">Email Address...</span><span class="btn">Sign Up</span></div>
</section>

<footer class="footer">
  <div class="f-contacts">
    <span><svg width="14" height="14" viewBox="0 0 24 24"><path fill="#fff" d="M12 2a7 7 0 0 0-7 7c0 5 7 13 7 13s7-8 7-13a7 7 0 0 0-7-7zm0 9.5A2.5 2.5 0 1 1 12 6a2.5 2.5 0 0 1 0 5.5z"/></svg>120 Harbour Lane Sydney</span>
    <span><svg width="14" height="14" viewBox="0 0 24 24"><path fill="#fff" d="M6.6 10.8a15 15 0 0 0 6.6 6.6l2.2-2.2c.3-.3.7-.4 1-.2 1.1.4 2.3.6 3.6.6.6 0 1 .4 1 1V20c0 .6-.4 1-1 1A17 17 0 0 1 3 4c0-.6.4-1 1-1h3.5c.6 0 1 .4 1 1 0 1.3.2 2.5.6 3.6.1.3 0 .7-.2 1z"/></svg>Phone: +(555) 010-2040</span>
    <span><svg width="14" height="14" viewBox="0 0 24 24"><path fill="#fff" d="M2 5h20v14H2z"/><path fill="none" stroke="#262626" stroke-width="2" d="M2 6l10 7 10-7"/></svg>Email: info@brightpathcoach.com</span>
  </div>
  <div class="socials" aria-label="Social links"><span></span><span></span><span></span><span></span><span></span></div>
  <div class="f-links">Home | About Us | How It Works | Application | Contact Us</div>
  <div class="copy">Copyright © 2018. All Rights Reserved.</div>
</footer>

</body>
</html>
```